Business card design for a teacher - double sided, sleek design.

My name is Lina and I am an online Arabic language teacher. I am looking for a beautiful business card design for my online teaching business.

The cards will be printed in 85mm x 55mm size.
The card can be either portrait or landscape.

The design should contain my logo on one side and information on the other.

The design needs to be clean and modern. Use of subtle Arabic geometric patterns would be nice. Icons for the social media information on the card should also match the design theme.

My logo font is Consolas, which is a Monospace font.

Business card design should be delivered with editable PSD or EPS files in the handover.

Thanks

Lina

----

Information on the back:

URL: www.speakwithnadia.net [this should stand out more than other details]
Email: info@speakwithnadia.net
Instagram: @speakwithnadia
Facebook: facebook.com/speakwithnadia
Skype: speakwithnadia

My brand colours are shown in the logo attached. These are:
- Teal green - 4DC9C1
- Mango yellow - FFD600

Target Market(s)

- Young professionals
- Expatriates
- Women and Men

Industry/Entity Type

Education

Contact Information for Business Card

Information on the back:

Skype: speakwithnadia

- Teal green - 4DC9C1
- Mango yellow - FFD600

Font styles to use
Other font styles liked:
• Any font complimentary to my logo font which is a Monospace font called Consolas.

Colors

Designer to choose colors to be used in the design.

Requirements
Must have
• - Aesthetically pleasing look
• - Complimentary design with existing logo
Nice to have
• Arabic geometrical patterns

```html
<!DOCTYPE html>
<html lang="en">
<head>
<meta charset="utf-8">
<title>Lina Lessons – Business Card</title>
<link rel="stylesheet" href="https://fonts.googleapis.com/css2?family=Open+Sans:wght@400;600&display=swap">
<style>
  :root {
    --backdrop: #2b2b2d;
    --card: #0c0c0d;
    --card-edge: #161618;
    --teal: #4dc9c1;
    --text: #e6e6e6;
    --divider: #2c2c2e;
    --icon-social: #3a8fd0;
  }
  * { box-sizing: border-box; margin: 0; padding: 0; }
  html, body {
    width: 1200px; height: 900px; overflow: hidden;
    background: var(--backdrop);
  }
  .canvas {
    position: relative; width: 1200px; height: 900px;
    display: flex; flex-direction: column; align-items: center;
    justify-content: center; gap: 40px;
  }
  .card {
    position: relative; width: 580px; height: 375px;
    background: linear-gradient(135deg, var(--card-edge), var(--card) 60%);
    overflow: hidden;
  }
  .card__band {
    position: absolute; left: 0; right: 0; bottom: 0; height: 10px;
    background: var(--teal);
  }

  /* Brand: plain circle + name in one colour and one weight */
  .brand { display: flex; align-items: center; gap: 18px; }
  .brand__dot { border-radius: 50%; background: var(--teal); flex: none; }
  .brand__name {
    font-family: "Open Sans", sans-serif; font-weight: 600;
    color: var(--teal); line-height: 1.2; white-space: nowrap;
  }

  /* Front */
  .card--front .brand {
    position: absolute; left: 0; right: 0; top: 140px; justify-content: center;
  }
  .card--front .brand__dot { width: 44px; height: 44px; }
  .card--front .brand__name { font-size: 40px; }
  .card--front .site {
    position: absolute; left: 0; right: 0; top: 262px; text-align: center;
    font-family: "Open Sans", sans-serif; font-weight: 600; font-size: 15px;
    letter-spacing: 0.12em; color: var(--text);
  }

  /* Back */
  .card--back .brand {
    position: absolute; left: 40px; top: 166px; gap: 12px;
  }
  .card--back .brand__dot { width: 26px; height: 26px; }
  .card--back .brand__name { font-size: 24px; }
  .card--back .divider {
    position: absolute; left: 262px; top: 70px; bottom: 70px; width: 1px;
    background: var(--divider);
  }
  .contacts {
    position: absolute; left: 292px; top: 104px; list-style: none;
    font-family: "Open Sans", sans-serif; font-size: 16px; color: var(--text);
  }
  .contacts__item { display: flex; align-items: center; gap: 10px; height: 27px; white-space: nowrap; }
  .contacts__item--site { font-weight: 600; color: #fff; }
  .contacts__group { margin-top: 16px; }
  .icon {
    width: 18px; height: 18px; flex: none; background: var(--teal);
    display: flex; align-items: center; justify-content: center;
  }
  .icon--social { background: var(--icon-social); }
</style>
</head>
<body>
<main class="canvas">

  <section class="card card--front" aria-label="Card front">
    <div class="brand">
      <span class="brand__dot"></span>
      <span class="brand__name">Lina Lessons</span>
    </div>
    <p class="site">www.speakwithnadia.net</p>
    <span class="card__band"></span>
  </section>

  <section class="card card--back" aria-label="Card back">
    <div class="brand">
      <span class="brand__dot"></span>
      <span class="brand__name">Lina Lessons</span>
    </div>
    <span class="divider"></span>
    <ul class="contacts">
      <li class="contacts__item">
        <span class="icon">
          <svg width="12" height="9" viewBox="0 0 12 9"><rect x="0.5" y="0.5" width="11" height="8" fill="none" stroke="#0c0c0d"/><path d="M0.5 0.5 6 5 11.5 0.5" fill="none" stroke="#0c0c0d"/></svg>
        </span>info@speakwithnadia.net
      </li>
      <li class="contacts__item contacts__item--site">
        <span class="icon">
          <svg width="12" height="12" viewBox="0 0 12 12"><circle cx="6" cy="6" r="5" fill="none" stroke="#0c0c0d"/><ellipse cx="6" cy="6" rx="2.2" ry="5" fill="none" stroke="#0c0c0d"/><path d="M1 6h10" stroke="#0c0c0d"/></svg>
        </span>www.speakwithnadia.net
      </li>
      <li class="contacts__item contacts__group">
        <span class="icon icon--social"></span>@speakwithnadia
      </li>
      <li class="contacts__item">
        <span class="icon icon--social"></span>friendnest.net/speakwithnadia
      </li>
      <li class="contacts__item">
        <span class="icon icon--social"></span>speakwithnadia
      </li>
    </ul>
    <span class="card__band"></span>
  </section>

</main>
</body>
</html>
```